Card Design for my dog training business Brightpaw Obedience

Need a business card design for my dog training business with my new logo. Want the card to come off professional yet fun. Want it to be very eye catchy as well. I normally have these at vet clinics, pet stores, and groomers. so need it to look better than my competitors.
Target Market(s)
dog owners
Industry/Entity Type
Dog Training
Contact Information for Business Card
needs logo, my name and info
Font styles to use
Serif
Colors
0255a3
ffffff
ec1f27
000000
333333
fbfbfb
Requirements
Must have
- Brightpaw Obedience
- Felix Orland
- 415 903 2276
- info@brightpawobedience.example
- www.brightpawobedience.example

```html
<!DOCTYPE html>
<html lang="en">
<head>
<meta charset="utf-8">
<title>Brightpaw Obedience — Business Card</title>
<link rel="stylesheet" href="https://fonts.googleapis.com/css2?family=EB+Garamond:ital,wght@0,500;1,400&family=Montserrat:wght@400;600&display=swap">
<style>
  :root {
    --brand-blue: #0255a3;
    --brand-blue-deep: #0a3f7e;
    --ink: #000000;
    --charcoal: #333333;
    --dark-panel: #232427;
    --paper: #fbfbfb;
    --white: #ffffff;
    --tint-blue: #d6e2ef;
    --stage: #3a3b3d;
  }
  * { box-sizing: border-box; margin: 0; padding: 0; }
  html, body { width: 1200px; height: 914px; overflow: hidden; }
  body {
    background: var(--stage);
    display: flex;
    align-items: center;
    justify-content: center;
    gap: 80px;
  }
  .card {
    position: relative;
    width: 400px;
    height: 760px;
    overflow: hidden;
    border-radius: 4px;
  }

  /* Front */
  .card--front {
    background: linear-gradient(180deg, var(--dark-panel) 0%, var(--dark-panel) 52%, #123f78 64%, var(--brand-blue) 100%);
  }
  .brand-mark {
    position: absolute;
    left: 0; right: 0;
    display: flex;
    align-items: center;
    justify-content: center;
    gap: 10px;
    font-family: "EB Garamond", serif;
    font-weight: 500;
    letter-spacing: 0.04em;
  }
  .brand-mark__dot {
    width: 14px; height: 14px;
    border-radius: 50%;
  }
  .card--front .brand-mark { top: 110px; color: var(--white); font-size: 28px; }
  .card--front .brand-mark__dot { background: var(--white); }
  .front-illustration {
    position: absolute;
    left: 30px; top: 250px;
    width: 340px; height: 250px;
    border-radius: 6px;
    background: linear-gradient(160deg, var(--white) 0%, #e4ecf5 100%);
    border: 6px solid var(--brand-blue);
  }
  .tagline {
    position: absolute;
    left: 0; right: 0; top: 560px;
    text-align: center;
    font-family: "EB Garamond", serif;
    font-style: italic;
    font-weight: 400;
    font-size: 30px;
    line-height: 1.25;
    color: var(--white);
  }

  /* Back */
  .card--back { background: var(--paper); }
  .card--back .brand-mark { top: 150px; color: var(--ink); font-size: 30px; }
  .card--back .brand-mark__dot { background: var(--ink); }
  .holder-name {
    position: absolute;
    left: 0; right: 0; top: 300px;
    text-align: center;
    font-family: "Montserrat", sans-serif;
    font-weight: 600;
    font-size: 26px;
    letter-spacing: 0.02em;
    color: var(--brand-blue);
    text-transform: uppercase;
  }
  .back-watermark {
    position: absolute;
    left: 30px; top: 370px;
    width: 340px; height: 330px;
    border-radius: 8px;
    background: radial-gradient(ellipse at center, var(--tint-blue) 0%, rgba(214,226,239,0.35) 70%, rgba(214,226,239,0) 100%);
  }
  .contact {
    position: absolute;
    left: 0; right: 0; top: 470px;
    text-align: center;
    font-family: "Montserrat", sans-serif;
    color: var(--charcoal);
  }
  .contact__icons {
    display: flex;
    justify-content: center;
    gap: 14px;
    margin-bottom: 12px;
  }
  .contact__icons svg { width: 18px; height: 18px; }
  .contact__line {
    font-size: 14px;
    line-height: 1.75;
  }
  .social {
    display: flex;
    justify-content: center;
    gap: 18px;
    margin-top: 20px;
  }
  .social__tile {
    width: 22px; height: 22px;
    border-radius: 3px;
    background: var(--brand-blue);
  }
</style>
</head>
<body>

  <section class="card card--front" aria-label="Card front">
    <div class="brand-mark">
      <span class="brand-mark__dot"></span>
      <span class="brand-mark__name">Brightpaw Obedience</span>
    </div>
    <div class="front-illustration" role="img" aria-label="Illustration of two dogs inside a Texas state outline"></div>
    <p class="tagline">“Training dogs across Texas<br>one dog at a time.”</p>
  </section>

  <section class="card card--back" aria-label="Card back">
    <div class="brand-mark">
      <span class="brand-mark__dot"></span>
      <span class="brand-mark__name">Brightpaw Obedience</span>
    </div>
    <h1 class="holder-name">Felix Orland</h1>
    <div class="back-watermark" role="img" aria-label="Faint pale-blue illustration of two dogs"></div>
    <div class="contact">
      <div class="contact__icons">
        <svg viewBox="0 0 24 24" aria-label="Phone" role="img"><path fill="#0255a3" d="M6.6 10.8a15.2 15.2 0 0 0 6.6 6.6l2.2-2.2c.3-.3.7-.4 1-.2 1.1.4 2.3.6 3.6.6.6 0 1 .4 1 1V20c0 .6-.4 1-1 1A17 17 0 0 1 3 4c0-.6.4-1 1-1h3.5c.6 0 1 .4 1 1 0 1.3.2 2.5.6 3.6.1.3 0 .7-.2 1z"/></svg>
        <svg viewBox="0 0 24 24" aria-label="Email" role="img"><rect x="2" y="5" width="20" height="14" rx="1" fill="#0255a3"/><path d="M3 6l9 7 9-7" fill="none" stroke="#fbfbfb" stroke-width="1.6"/></svg>
        <svg viewBox="0 0 24 24" aria-label="Website" role="img"><g fill="none" stroke="#0255a3" stroke-width="1.8"><circle cx="12" cy="12" r="9"/><ellipse cx="12" cy="12" rx="4" ry="9"/><path d="M3 12h18M5 7h14M5 17h14"/></g></svg>
      </div>
      <p class="contact__line">415 903 2276</p>
      <p class="contact__line">info@brightpawobedience.example</p>
      <p class="contact__line">www.brightpawobedience.example</p>
      <div class="social">
        <span class="social__tile" aria-hidden="true"></span>
        <span class="social__tile" aria-hidden="true"></span>
      </div>
    </div>
  </section>

</body>
</html>
```